Brochure for a website accessibility report

This brochure is related to a report that www.qelvantrix.org sell. The report shows the results of an automated audit of a websites accessibility. It shows details of issues found with screen shots, examples of code and provides remediation advice.

The brochure will be a pdf 8.5 inches by 11 inches. It can be anywhere from 6 to 10 pages.

The FlintVue™ name itself should be “Bree Serif” font. The fonts, styles, colors and sizes are up to you.

The images used and logo of the Office of Digital Reachworks and K7P logo are upload

We highlighted in blue page extracts from the report we sell. Do not use the blue highlight, it is merely there to show you where the specific examples of the report we sell are vs the other content in the report. The areas in blue which show the content from the actual report should be shown as an extract of the actual page of the report. You have flexibility to change the layout and the way the content look.

The red square callouts over the blue content are callouts that describe the specific page extracts. We used it as a red callout only so that you would be able to see it. You should change the specific location, look and feel of the callout to be appropriate

Target Market(s)

Marketing and Technical people

Industry/Entity Type

Information Technology

Font styles to use
Sans Serif

Colors

Designer to choose colors to be used in the design.

Requirements
Should not have
• wheelchairs, images of blind people

```html
<!DOCTYPE html>
<html lang="en">
<head>
<meta charset="utf-8">
<title>FlintVue™ 2019 Brochure – Office of Digital Reachworks</title>
<link rel="stylesheet" href="https://fonts.googleapis.com/css2?family=Bree+Serif&family=Raleway:wght@400;600;700;800&display=swap">
<style>
  :root {
    --stage: #dedede;
    --paper: #f7f7f7;
    --green: #2fb26b;
    --ink: #141414;
    --navy: #1f3b6e;
    --white: #ffffff;
    --sky-top: #d3d9e6;
    --sky-mid: #8fa9cf;
    --sky-low: #4c78b2;
    --city: #2a3c58;
  }
  * { box-sizing: border-box; margin: 0; padding: 0; }
  html, body { width: 1200px; height: 840px; overflow: hidden; background: var(--stage); }
  .canvas { position: relative; width: 1200px; height: 840px; }

  .cover {
    position: absolute; left: 300px; top: 32px; width: 600px; height: 776px;
    background: var(--paper); overflow: hidden;
    box-shadow: 0 10px 30px rgba(0,0,0,.18);
  }

  .org-name {
    position: absolute; left: 56px; top: 58px;
    display: flex; align-items: center; gap: 10px;
    font-family: "Raleway", Arial, sans-serif; font-weight: 800; font-size: 17px;
    color: var(--ink); text-transform: uppercase; letter-spacing: .5px;
  }
  .org-name .square { width: 16px; height: 16px; background: var(--ink); flex: none; }

  .site-mark {
    position: absolute; right: 36px; top: 36px;
    display: flex; align-items: center; gap: 8px;
    font-family: "Raleway", Arial, sans-serif; font-weight: 700; font-size: 14px; color: var(--navy);
  }
  .site-mark .dot { width: 16px; height: 16px; border-radius: 50%; background: var(--navy); flex: none; }

  .mission-quote {
    position: absolute; right: 36px; top: 70px; width: 196px;
    font-family: "Raleway", Arial, sans-serif; color: var(--navy);
  }
  .mission-quote .top { display: flex; align-items: flex-end; gap: 8px; }
  .mission-quote .mark { color: var(--green); font-family: "Bree Serif", Georgia, serif; font-size: 24px; line-height: 1; }
  .mission-quote .rule { flex: 1; height: 1px; background: var(--green); margin-bottom: 6px; }
  .mission-quote p { font-size: 11px; font-weight: 600; line-height: 1.4; margin: 4px 0 6px 8px; }
  .mission-quote .bottom { display: flex; align-items: center; gap: 8px; }
  .mission-quote .web { font-size: 10.5px; font-weight: 700; }
  .mission-quote .bottom .rule { margin: 0; }

  .hero-visual {
    position: absolute; left: 0; top: 196px; width: 565px; height: 456px;
    background: linear-gradient(172deg, var(--sky-top) 0%, var(--sky-mid) 35%, var(--sky-low) 68%, var(--city) 100%);
  }

  .product-name {
    position: absolute; left: 112px; top: 568px;
    font-family: "Bree Serif", Georgia, serif; font-size: 72px; line-height: 1;
    color: var(--white); letter-spacing: 1px;
  }

  .title-band {
    position: absolute; left: 0; top: 652px; width: 565px; height: 82px;
    background: var(--green);
  }
  .edition {
    position: absolute; left: 100px; top: 10px;
    font-family: "Bree Serif", Georgia, serif; font-weight: 400; font-size: 28px; color: var(--white);
  }
  .publisher {
    position: absolute; left: 100px; top: 50px;
    font-family: "Raleway", Arial, sans-serif; font-weight: 800; font-size: 12px;
    color: var(--ink); text-transform: uppercase; letter-spacing: .4px;
  }
  .band-contact {
    position: absolute; right: 16px; top: 12px; text-align: right; width: 180px;
    font-family: "Raleway", Arial, sans-serif; color: var(--white);
  }
  .band-contact .web { font-weight: 800; font-size: 14px; margin-bottom: 4px; }
  .band-contact p { font-size: 10px; line-height: 1.3; }
</style>
</head>
<body>
<main class="canvas">
  <article class="cover">
    <h1 class="org-name"><span class="square"></span><span>Office of Digital Reachworks</span></h1>

    <div class="site-mark"><span class="dot"></span><span>qelvantrix.org</span></div>

    <blockquote class="mission-quote">
      <div class="top"><span class="mark">&ldquo;</span><span class="rule"></span></div>
      <p>The mission of the ODR team is to make the Internet accessible for everyone.</p>
      <div class="bottom"><span class="rule"></span><span class="web">www.qelvantrix.org</span><span class="mark">&rdquo;</span></div>
    </blockquote>

    <div class="hero-visual" role="img" aria-label="Photo of a laptop in front of a city skyline at dusk, overlaid with streams of binary digits and a faint world map"></div>

    <div class="product-name">FlintVue™</div>

    <section class="title-band">
      <h2 class="edition">2019 Brochure</h2>
      <div class="publisher">Office of Digital Reachworks</div>
      <div class="band-contact">
        <div class="web">www.qelvantrix.org</div>
        <p>The mission of the ODR team is to make the Internet accessible for everyone.</p>
      </div>
    </section>
  </article>
</main>
</body>
</html>
```